Harlow Mechanical Contractors needs a Website

Create basic website for commercial plumbing and mechanical contractor; to include pictures of works in progress and completed works, description of all services offered and geographical locations and licenses

Target Market(s)

General Contractors, Real Estate Developers, Construction Companies

Industry/Entity Type

Construction

Coding

Coded - Design and coding required

Number of Pages Required

5+ page

• See logo attached to project

Colors
0392cd

```html
<!DOCTYPE html>
<html lang="en">
<head>
<meta charset="utf-8">
<title>Harlow Mechanical Contractors</title>
<link rel="stylesheet" href="https://fonts.googleapis.com/css2?family=Open+Sans:wght@400;600;700&family=Oswald:wght@400;500&family=Roboto+Condensed:wght@400;700&family=Roboto:wght@400;500&display=swap">
<style>
:root{
  --brand:#1f5580;
  --brand-dark:#1c4f78;
  --accent:#0392cd;
  --accent-btn:#2a8fc4;
  --ink:#2b2b2b;
  --muted:#6a6a6a;
  --line:#e3e6ea;
  --pale:#edf3f8;
  --white:#ffffff;
  --footer-bar:#333436;
}
*{box-sizing:border-box;margin:0;padding:0}
html,body{width:1200px;height:2731px;overflow:hidden}
body{position:relative;background:var(--white);font-family:"Open Sans",Arial,sans-serif;color:var(--ink)}
.abs{position:absolute}

/* header */
.site-header{position:absolute;left:0;top:0;width:1200px;height:128px;background:linear-gradient(#fff,#f4f5f7);box-shadow:0 1px 3px rgba(0,0,0,.15);z-index:2}
.brand{position:absolute;left:98px;top:20px;display:flex;align-items:center;gap:12px}
.brand-mark{width:86px;height:86px;border-radius:50%;background:var(--brand)}
.brand-name{font-family:"Roboto Condensed",Arial,sans-serif;font-weight:700;font-size:19px;line-height:19px;color:var(--brand);text-transform:uppercase}
.top-contact{position:absolute;right:100px;top:23px;display:flex;gap:26px;font-family:Roboto,Arial,sans-serif;font-size:14px;color:#333}
.top-contact span{display:flex;align-items:center;gap:8px}
.top-contact .mail{color:var(--accent)}
.main-nav{position:absolute;top:64px;left:0;width:1200px}
.nav-item{position:absolute;font-family:Roboto,Arial,sans-serif;font-size:15px;color:#222;text-transform:uppercase;line-height:20px}
.nav-item small{display:block;font-size:12px;color:#777;text-transform:none}
.nav-item.active{color:var(--brand)}
.nav-item + .nav-item::before{content:"";position:absolute;left:-20px;top:-4px;width:1px;height:48px;background:var(--line)}

/* hero */
.hero{position:absolute;left:0;top:128px;width:1200px;height:519px;background:linear-gradient(180deg,#3a4350 0%,#5d6a78 28%,#2a3038 60%,#1b1e23 100%)}
.hero-title{position:absolute;top:203px;width:100%;text-align:center;font-family:Oswald,Arial,sans-serif;font-weight:500;font-size:38px;color:#fff;letter-spacing:.5px}
.hero-text{position:absolute;top:257px;left:260px;width:680px;text-align:center;font-size:14px;line-height:22px;color:#fff}
.hero-btn{position:absolute;top:320px;left:532px;width:136px;height:36px;border:1px solid #fff;color:#fff;font-family:Roboto,Arial,sans-serif;font-size:13px;display:flex;align-items:center;justify-content:center;background:rgba(0,0,0,.2)}
.hero-arrow{position:absolute;top:222px}

/* welcome */
.section-title{position:absolute;width:100%;text-align:center;font-family:"Roboto Condensed",Arial,sans-serif;font-size:31px;color:#222;text-transform:uppercase}
.section-title em{font-style:normal;color:var(--brand)}
.welcome-text{position:absolute;top:747px;left:150px;width:900px;text-align:center;font-size:11.5px;line-height:19px;color:#555}
.feature{position:absolute;top:856px;width:330px;height:130px}
.feature-icon{position:absolute;left:0;top:0;width:96px;height:96px;border-radius:50%;background:var(--brand);display:flex;align-items:center;justify-content:center}
.feature h3{position:absolute;left:113px;top:12px;font-family:Roboto,Arial,sans-serif;font-weight:400;font-size:19px;color:#222;text-transform:uppercase}
.feature p{position:absolute;left:113px;top:50px;width:205px;font-size:11.5px;line-height:20px;color:#777}

/* services */
.services{position:absolute;left:0;top:1038px;width:1200px;height:552px;background:var(--pale)}
.service-card{position:absolute;top:109px;width:315px;height:370px;background:#fff;border:1px solid #d8dde3}
.service-photo{width:100%;height:191px}
.service-card h3{margin-top:16px;text-align:center;font-family:Roboto,Arial,sans-serif;font-weight:400;font-size:19px;text-transform:uppercase;color:#222}
.service-card p{margin:10px auto 0;width:270px;text-align:center;font-size:11.5px;line-height:20px;color:#666}
.btn-small{position:absolute;left:108px;top:314px;width:99px;height:30px;background:var(--brand);color:#fff;font-size:13px;display:flex;align-items:center;justify-content:center;border-radius:2px}

/* call to action */
.cta{position:absolute;left:0;top:1590px;width:1200px;height:362px;background:linear-gradient(90deg,#f3f6f8,#e6ecef 60%,#dfe5e9)}
.cta-photo-left{position:absolute;left:0;top:0;width:342px;height:362px;background:linear-gradient(135deg,#1f6fd0,#2c86e4 60%,#5aa2e8);clip-path:polygon(0 0,100% 0,30% 100%,0 100%)}
.cta-photo-right{position:absolute;left:880px;top:12px;width:230px;height:350px;background:linear-gradient(180deg,#e0b63a 0%,#6a7f94 30%,#4a5d72 70%,#2b3440 100%);border-radius:90px 90px 0 0}
.cta h2{position:absolute;top:83px;left:380px;width:520px;text-align:center;font-family:"Open Sans",Arial,sans-serif;font-weight:700;font-size:47px;color:var(--brand-dark)}
.cta .cta-sub{position:absolute;top:148px;left:380px;width:520px;text-align:center;font-size:30px;color:#333}
.cta-btn{position:absolute;top:209px;left:526px;width:213px;height:44px;background:var(--accent-btn);color:#fff;font-family:Roboto,Arial,sans-serif;font-size:16px;display:flex;align-items:center;justify-content:center;text-transform:uppercase;border-radius:2px}

/* blog */
.post{position:absolute;top:2060px;width:312px}
.post-photo{width:100%;height:151px}
.post h3{margin-top:16px;font-family:Roboto,Arial,sans-serif;font-weight:400;font-size:16px;color:#222}
.post-meta{margin-top:10px;font-size:12.5px;color:#444;display:flex;align-items:center;gap:7px}
.post p{margin-top:10px;font-size:12px;line-height:22px;color:#555}
.post-rule{margin-top:14px;height:1px;background:var(--line)}

/* footer */
.site-footer{position:absolute;left:0;top:2404px;width:1200px;height:275px;background:var(--brand)}
.footer-brand{position:absolute;left:98px;top:47px;display:flex;align-items:center;gap:12px}
.footer-brand .brand-mark{width:86px;height:86px;background:#fff}
.footer-brand .brand-name{color:#fff}
.social{position:absolute;left:126px;top:164px;display:flex;gap:10px}
.social span{width:26px;height:26px;border-radius:50%;background:#fff;opacity:.9}
.footer-col h4{position:absolute;top:47px;font-family:"Roboto Condensed",Arial,sans-serif;font-weight:400;font-size:18px;color:#fff;text-transform:uppercase}
.contact-list{position:absolute;left:357px;top:94px;list-style:none;color:#fff;font-size:13px}
.contact-list li{display:flex;gap:14px;align-items:flex-start;height:31px;line-height:20px}
.contact-list svg{margin-top:4px;flex:none}
.quick-links{position:absolute;left:672px;top:96px;list-style:none;color:#fff;font-size:11.5px;text-transform:uppercase}
.quick-links li{height:24px;display:flex;align-items:center;gap:12px}
.newsletter-text{position:absolute;left:852px;top:94px;width:260px;font-size:12px;line-height:20px;color:#fff}
.newsletter-input{position:absolute;left:852px;top:142px;width:248px;height:40px;background:#fff;font-size:11px;color:#444;padding:12px 14px}
.newsletter-btn{position:absolute;left:852px;top:191px;width:91px;height:37px;background:#1f2326;color:#fff;font-size:11px;display:flex;align-items:center;justify-content:center;text-transform:uppercase}
.footer-bar{position:absolute;left:0;top:2679px;width:1200px;height:52px;background:var(--footer-bar);color:#fff;font-size:12px;text-align:center;line-height:52px}
</style>
</head>
<body>

<header class="site-header">
  <div class="brand">
    <div class="brand-mark"></div>
    <div class="brand-name">Harlow<br>Mechanical<br>Contractors</div>
  </div>
  <div class="top-contact">
    <span><svg width="13" height="13" viewBox="0 0 24 24"><path fill="#333" d="M6.6 10.8a15 15 0 0 0 6.6 6.6l2.2-2.2c.3-.3.7-.4 1-.2 1.1.4 2.3.6 3.6.6.6 0 1 .4 1 1V20c0 .6-.4 1-1 1A17 17 0 0 1 3 4c0-.6.4-1 1-1h3.5c.6 0 1 .4 1 1 0 1.3.2 2.5.6 3.6.1.3 0 .7-.2 1z"/></svg>+1 800 555 0110</span>
    <span class="mail"><svg width="15" height="12" viewBox="0 0 24 18"><rect x="1" y="1" width="22" height="16" fill="none" stroke="#333" stroke-width="2"/><path d="M1 1l11 9 11-9" fill="none" stroke="#333" stroke-width="2"/></svg>info@harlowmechanicalcontractors.com</span>
  </div>
  <nav class="main-nav">
    <a class="nav-item active" style="left:481px">Home<small>Start page</small></a>
    <a class="nav-item" style="left:601px">About Us<small>Who we are</small></a>
    <a class="nav-item" style="left:739px">Services<small>What we offer</small></a>
    <a class="nav-item" style="left:878px">Testimonials<small>Reviews</small></a>
    <a class="nav-item" style="left:1036px">Contact<small>Get in touch</small></a>
  </nav>
</header>

<section class="hero" role="img" aria-label="Dusk skyline of a dense city with high-rise towers">
  <svg class="hero-arrow" style="left:52px" width="14" height="24" viewBox="0 0 14 24"><path d="M12 2L3 12l9 10" fill="none" stroke="#fff" stroke-width="2.5"/></svg>
  <svg class="hero-arrow" style="left:1138px" width="14" height="24" viewBox="0 0 14 24"><path d="M2 2l9 10-9 10" fill="none" stroke="#fff" stroke-width="2.5"/></svg>
  <h1 class="hero-title">HARLOW MECHANICAL CONTRACTORS</h1>
  <p class="hero-text">Sed ut perspiciatis unde omnis iste natus error sit voluptatem accusantium doloremque laudantium, totam rem aperiam, eaque ipsa quae ab illo inventore veritatis et quasi architecto beatae</p>
  <a class="hero-btn">GET MORE INFO</a>
</section>

<h2 class="section-title" style="top:696px">Welcome to <em>Harlow Mechanical Contractors</em></h2>
<p class="welcome-text">Lorem ipsum dolor sit amet, consectetur adipiscing elit, sed do eiusmod tempor incididunt ut labore et dolore magna aliqua. Ut enim ad minim veniam, quis nostrud exercitation ullamco laboris nisi ut aliquip ex ea commodo consequat. Duis aute irure dolor in reprehenderit in voluptate velit esse cillum dolore eu fugiat nulla pariatur. Excepteur sint occaecat cupidatat non proident, sunt in culpa qui officia deserunt mollit anim id est laborum</p>

<div class="feature" style="left:98px">
  <div class="feature-icon"><svg width="40" height="40" viewBox="0 0 24 24"><path d="M14.7 6.3a4 4 0 0 0-5.4 5.2L3 17.8 6.2 21l6.3-6.3a4 4 0 0 0 5.2-5.4l-2.5 2.5-2.3-.7-.7-2.3z" fill="#fff"/></svg></div>
  <h3>Maintenance</h3>
  <p>Sed ut perspiciatis unde omnis natus error sit voluptatem accusantium doloremque laudantium, totam rem aperiam, eaque ipsa</p>
</div>
<div class="feature" style="left:448px">
  <div class="feature-icon"><svg width="40" height="40" viewBox="0 0 24 24"><path d="M3 7h11v3H9v3H6V10H3zM14 6h4v5h2v3h-6z" fill="#fff"/><path d="M17 16c0 2 1 3 1 4a1 1 0 0 1-2 0c0-1 1-2 1-4z" fill="#fff"/></svg></div>
  <h3>New Installation</h3>
  <p>Sed ut perspiciatis unde omnis natus error sit voluptatem accusantium doloremque laudantium, totam rem aperiam, eaque ipsa</p>
</div>
<div class="feature" style="left:790px">
  <div class="feature-icon"><svg width="40" height="40" viewBox="0 0 24 24"><circle cx="10" cy="10" r="6" fill="none" stroke="#fff" stroke-width="2.5"/><path d="M14.5 14.5L21 21" stroke="#fff" stroke-width="3"/></svg></div>
  <h3>Inspections</h3>
  <p>Sed ut perspiciatis unde omnis natus error sit voluptatem accusantium doloremque laudantium, totam rem aperiam, eaque ipsa</p>
</div>

<section class="services">
  <h2 class="section-title" style="top:46px">Plumbing Services</h2>
  <article class="service-card" style="left:98px">
    <div class="service-photo" role="img" aria-label="Bright open-plan office with rows of desks" style="background:linear-gradient(180deg,#f0ede6,#d9d4cb 55%,#5a5550 80%,#cfc9c0)"></div>
    <h3>Large Offices</h3>
    <p>Sed ut perspiciatis unde omnis iste natus error sit voluptatem accusantium doloremque laudantium, totam rem aperiam, eaque ipsa quae</p>
    <a class="btn-small">Read More</a>
  </article>
  <article class="service-card" style="left:443px">
    <div class="service-photo" role="img" aria-label="Modern condominium tower under a blue sky" style="background:linear-gradient(180deg,#2f7fd6,#7fb5e8 50%,#e9ecef 70%,#6b9a3e)"></div>
    <h3>Condominiums</h3>
    <p>Sed ut perspiciatis unde omnis iste natus error sit voluptatem accusantium doloremque laudantium, totam rem aperiam, eaque ipsa quae</p>
    <a class="btn-small">Read More</a>
  </article>
  <article class="service-card" style="left:785px">
    <div class="service-photo" role="img" aria-label="Workers in an industrial plant among pipework" style="background:linear-gradient(135deg,#c9d2da,#7d8c9a 50%,#3e4d5f)"></div>
    <h3>Industrial Projects</h3>
    <p>Sed ut perspiciatis unde omnis iste natus error sit voluptatem accusantium doloremque laudantium, totam rem aperiam, eaque ipsa quae</p>
    <a class="btn-small">Read More</a>
  </article>
</section>

<section class="cta">
  <div class="cta-photo-left" role="img" aria-label="Plumbing fittings and taps laid out on a blue surface"></div>
  <div class="cta-photo-right" role="img" aria-label="Plumber in a hard hat holding a toolbox"></div>
  <h2>NEED A PLUMBER?</h2>
  <p class="cta-sub">You’re in the right place.</p>
  <a class="cta-btn">Book an Appointment</a>
</section>

<h2 class="section-title" style="top:1991px">Recent <em>Blog</em></h2>
<article class="post" style="left:98px">
  <div class="post-photo" role="img" aria-label="Technicians working at a bench" style="background:linear-gradient(135deg,#6b4a3a,#c9c3bd 55%,#8a8f96)"></div>
  <h3>Nemo enim ipsam voluptatem</h3>
  <div class="post-meta"><svg width="12" height="12" viewBox="0 0 24 24"><circle cx="12" cy="12" r="10" fill="none" stroke="#333" stroke-width="2.5"/><path d="M12 6v6l4 2" fill="none" stroke="#333" stroke-width="2.5"/></svg>3 minutes ago, 0 comments</div>
  <p>Lorem ipsum dolor sit amet, consectetur adipiscing elit, sed do eiusmod tempor incididunt ut labore et dolore</p>
  <div class="post-rule"></div>
</article>
<article class="post" style="left:450px;width:308px">
  <div class="post-photo" role="img" aria-label="Engineer among steel pipework" style="background:linear-gradient(135deg,#dfe4e8,#8d98a3 50%,#3d4650)"></div>
  <h3>Nemo enim ipsam voluptatem</h3>
  <div class="post-meta"><svg width="12" height="12" viewBox="0 0 24 24"><circle cx="12" cy="12" r="10" fill="none" stroke="#333" stroke-width="2.5"/><path d="M12 6v6l4 2" fill="none" stroke="#333" stroke-width="2.5"/></svg>3 minutes ago, 0 comments</div>
  <p>Lorem ipsum dolor sit amet, consectetur adipiscing elit, sed do eiusmod tempor incididunt ut labore et dolore</p>
  <div class="post-rule"></div>
</article>
<article class="post" style="left:792px;width:308px">
  <div class="post-photo" role="img" aria-label="Hard hat in front of a refinery at sunset" style="background:linear-gradient(180deg,#3b5a8a,#e07a3a 55%,#2a2a2e)"></div>
  <h3>Nemo enim ipsam voluptatem</h3>
  <div class="post-meta"><svg width="12" height="12" viewBox="0 0 24 24"><circle cx="12" cy="12" r="10" fill="none" stroke="#333" stroke-width="2.5"/><path d="M12 6v6l4 2" fill="none" stroke="#333" stroke-width="2.5"/></svg>3 minutes ago, 0 comments</div>
  <p>Lorem ipsum dolor sit amet, consectetur adipiscing elit, sed do eiusmod tempor incididunt ut labore et dolore</p>
  <div class="post-rule"></div>
</article>

<footer class="site-footer">
  <div class="footer-brand">
    <div class="brand-mark"></div>
    <div class="brand-name">Harlow<br>Mechanical<br>Contractors</div>
  </div>
  <div class="social"><span></span><span></span><span></span><span></span></div>

  <div class="footer-col"><h4 style="left:357px">Contact Info</h4></div>
  <ul class="contact-list">
    <li><svg width="13" height="13" viewBox="0 0 24 24"><path fill="#fff" d="M6.6 10.8a15 15 0 0 0 6.6 6.6l2.2-2.2c.3-.3.7-.4 1-.2 1.1.4 2.3.6 3.6.6.6 0 1 .4 1 1V20c0 .6-.4 1-1 1A17 17 0 0 1 3 4c0-.6.4-1 1-1h3.5c.6 0 1 .4 1 1 0 1.3.2 2.5.6 3.6.1.3 0 .7-.2 1z"/></svg>Toll Free: 1.800.555.0142</li>
    <li><svg width="13" height="13" viewBox="0 0 24 24"><rect x="3" y="8" width="18" height="12" fill="#fff"/><rect x="7" y="3" width="10" height="6" fill="#fff"/></svg>Fax: +1.800.555.0187</li>
    <li><svg width="13" height="11" viewBox="0 0 24 18"><rect x="1" y="1" width="22" height="16" fill="#fff"/><path d="M1 1l11 9 11-9" fill="none" stroke="#1f5580" stroke-width="2"/></svg>Email: info@harlowmechanical.com</li>
    <li><svg width="13" height="15" viewBox="0 0 24 28"><path fill="#fff" d="M12 0a10 10 0 0 0-10 10c0 7 10 18 10 18s10-11 10-18A10 10 0 0 0 12 0zm0 14a4 4 0 1 1 0-8 4 4 0 0 1 0 8z"/></svg>418 Alder Avenue, Suite 120<br>Millbrook, Oregon</li>
  </ul>

  <div class="footer-col"><h4 style="left:672px">Quick Links</h4></div>
  <ul class="quick-links">
    <li><svg width="5" height="8" viewBox="0 0 5 8"><path d="M0 0l5 4-5 4z" fill="#fff"/></svg>Home</li>
    <li><svg width="5" height="8" viewBox="0 0 5 8"><path d="M0 0l5 4-5 4z" fill="#fff"/></svg>About Us</li>
    <li><svg width="5" height="8" viewBox="0 0 5 8"><path d="M0 0l5 4-5 4z" fill="#fff"/></svg>Our Services</li>
    <li><svg width="5" height="8" viewBox="0 0 5 8"><path d="M0 0l5 4-5 4z" fill="#fff"/></svg>Blog</li>
    <li><svg width="5" height="8" viewBox="0 0 5 8"><path d="M0 0l5 4-5 4z" fill="#fff"/></svg>Contact</li>
  </ul>

  <div class="footer-col"><h4 style="left:852px">Join Our Newsletter</h4></div>
  <p class="newsletter-text">Excepteur sint occaecat cupidatat non proident, sunt in culpa qui</p>
  <div class="newsletter-input">Enter Name</div>
  <a class="newsletter-btn">Subscribe</a>
</footer>
<div class="footer-bar">© 2016 Harlow mechanical contractors... All Rights Reserved.</div>

</body>
</html>
```